wealth management firm, professional group, new model

we have a logo that works but we need a card, white background using our colors...clean look

our tag line if can be used in

The Bridge From Client to Owner

```html
<!DOCTYPE html>
<html lang="en">
<head>
<meta charset="utf-8">
<title>Arvel Wealth Partners – Business Card</title>
<link href="https://fonts.googleapis.com/css2?family=Montserrat:wght@400;500;700&display=swap" rel="stylesheet">
<style>
  :root {
    --navy: #172e55;
    --navy-emboss: #2a4a7e;
    --ink: #1a2f57;
    --white: #ffffff;
    --stage: #2a2a2c;
  }
  * { box-sizing: border-box; margin: 0; padding: 0; }
  html, body { width: 1200px; height: 875px; overflow: hidden; }
  body {
    background: var(--stage);
    font-family: "Montserrat", sans-serif;
    display: flex;
    align-items: center;
    justify-content: center;
    gap: 48px;
  }
  .card {
    width: 525px;
    height: 300px;
    border-radius: 18px;
    position: relative;
    overflow: hidden;
  }
  .card--front {
    background: var(--navy);
    display: flex;
    flex-direction: column;
    align-items: center;
    justify-content: center;
    gap: 18px;
  }
  .brand {
    display: flex;
    align-items: center;
    justify-content: center;
    gap: 12px;
    font-weight: 500;
    line-height: 1;
    white-space: nowrap;
  }
  .brand__dot {
    width: 14px;
    height: 14px;
    border-radius: 50%;
    background: currentColor;
    flex: none;
  }
  .card--front .brand { color: var(--navy-emboss); font-size: 34px; }
  .tagline {
    color: var(--navy-emboss);
    font-size: 15px;
    font-weight: 400;
  }
  .card--back { background: var(--white); }
  .card--back .brand {
    color: var(--ink);
    font-size: 28px;
    position: absolute;
    top: 46px;
    left: 0;
    right: 0;
  }
  .card--back .brand__dot { width: 12px; height: 12px; }
  .person {
    position: absolute;
    top: 118px;
    left: 0; right: 0;
    text-align: center;
    color: var(--ink);
  }
  .person__name { font-size: 24px; font-weight: 700; letter-spacing: 0.01em; }
  .person__title { font-size: 14px; font-weight: 400; margin-top: 4px; }
  .contacts {
    position: absolute;
    top: 202px;
    left: 0; right: 0;
    display: flex;
    justify-content: center;
    align-items: center;
    gap: 8px;
    font-size: 11px;
    color: var(--ink);
    white-space: nowrap;
  }
  .contacts__item { display: flex; align-items: center; gap: 5px; }
  .contacts__icon { width: 12px; height: 12px; fill: var(--ink); flex: none; }
  .contacts__sep { opacity: 0.8; }
  .address-band {
    position: absolute;
    left: 0; right: 0; bottom: 0;
    height: 50px;
    background: var(--navy);
    color: var(--white);
    font-size: 13px;
    display: flex;
    align-items: center;
    justify-content: center;
  }
</style>
</head>
<body>
  <section class="card card--front" aria-label="Card front">
    <div class="brand">
      <span class="brand__dot" aria-hidden="true"></span>
      <span class="brand__name">Arvel Wealth Partners</span>
    </div>
    <p class="tagline">The Bridge From Client to Owner</p>
  </section>

  <section class="card card--back" aria-label="Card back">
    <div class="brand">
      <span class="brand__dot" aria-hidden="true"></span>
      <span class="brand__name">Arvel Wealth Partners</span>
    </div>
    <div class="person">
      <p class="person__name">DANA WHITFIELD</p>
      <p class="person__title">General Manager</p>
    </div>
    <div class="contacts">
      <span class="contacts__item">
        <svg class="contacts__icon" viewBox="0 0 16 16" aria-hidden="true"><path d="M1 3h14v10H1z M1 3l7 6 7-6" fill="none" stroke="#1a2f57" stroke-width="1.6"/></svg>
        info@arvelwealth.com
      </span>
      <span class="contacts__sep">|</span>
      <span class="contacts__item">
        <svg class="contacts__icon" viewBox="0 0 16 16" aria-hidden="true"><path d="M3 1h3l1.5 4-2 1.3a9 9 0 0 0 4.2 4.2L11 8.5l4 1.5v3a2 2 0 0 1-2 2A12 12 0 0 1 1 3a2 2 0 0 1 2-2z"/></svg>
        (555) 014-2290
      </span>
      <span class="contacts__sep">|</span>
      <span class="contacts__item">
        <svg class="contacts__icon" viewBox="0 0 16 16" aria-hidden="true"><circle cx="8" cy="8" r="6.5" fill="none" stroke="#1a2f57" stroke-width="1.4"/><path d="M1.5 8h13M8 1.5c-3 3.5-3 9.5 0 13M8 1.5c3 3.5 3 9.5 0 13" fill="none" stroke="#1a2f57" stroke-width="1.2"/></svg>
        www.arvelwealth.com
      </span>
    </div>
    <div class="address-band">240 Harbor Crest Way, Suite 100, Fairview, TN 38000</div>
  </section>
</body>
</html>
```